Website Revamp: Bravoly.com

Just got a new logo looking for a web design to go with the business. I need the photoshop files and stock photos. No Word Press Please.

```html
<!DOCTYPE html>
<html lang="en">
<head>
<meta charset="utf-8">
<title>Bravoly — Auto Recycling</title>
<link rel="stylesheet" href="https://fonts.googleapis.com/css2?family=Exo+2:ital,wght@0,400;0,600;0,700;0,800;1,700;1,800&family=Lato:wght@400;700;900&display=swap">
<style>
:root{
  --green:#7dc03a;
  --green-dark:#6aab2c;
  --ink:#333333;
  --text:#555555;
  --muted:#777777;
  --light:#f2f2f2;
  --slate:#6b7572;
  --white:#ffffff;
  --rule:#d8d8d8;
}
*{margin:0;padding:0;box-sizing:border-box}
html,body{width:1200px;height:3667px;overflow:hidden;background:var(--white)}
body{position:relative;font-family:"Lato",sans-serif;color:var(--text)}
.abs{position:absolute}
.head{font-family:"Exo 2",sans-serif}

/* header */
.site-header{position:absolute;left:0;top:0;width:1200px;height:88px;background:var(--white)}
.brand{position:absolute;display:flex;align-items:center;gap:12px}
.brand-dot{width:64px;height:64px;border-radius:50%;background:var(--green)}
.brand-name{font-family:"Exo 2",sans-serif;font-weight:800;color:var(--green);font-size:44px;letter-spacing:1px;line-height:1}
.main-nav a{position:absolute;top:37px;font-family:"Exo 2",sans-serif;font-size:14px;font-weight:600;color:#6c6c6c;text-decoration:none;letter-spacing:.2px}
.main-nav a.active{color:var(--ink);font-weight:700}
.nav-bar{position:absolute;left:429px;top:0;width:75px;height:3px;background:var(--green)}

/* hero */
.hero{position:absolute;left:0;top:88px;width:1200px;height:619px;background:linear-gradient(135deg,#7d8790 0%,#4c525a 35%,#9aa0a6 60%,#5b5f68 85%,#3f444b 100%)}
.hero-circle{position:absolute;left:93px;top:101px;width:398px;height:398px;border-radius:50%;background:var(--green);text-align:center;color:var(--white)}
.hero-kicker{margin-top:112px;font-family:"Exo 2",sans-serif;font-size:28px;font-weight:400;letter-spacing:1px}
.hero-title{font-family:"Exo 2",sans-serif;font-size:58px;font-weight:800;line-height:1;margin-top:6px}
.hero-text{font-size:17px;line-height:26px;margin:18px auto 0;width:310px}
.btn{display:inline-flex;align-items:center;justify-content:center;font-family:"Lato",sans-serif;font-weight:900;font-size:14px;border-radius:30px;text-transform:uppercase}
.btn-white{background:var(--white);color:var(--ink)}
.hero-btn{width:172px;height:46px;margin-top:20px;font-size:15px}
.slide-arrow{position:absolute;top:287px;width:42px;height:42px;border-radius:50%;background:rgba(255,255,255,.85)}

/* about */
.about{position:absolute;left:0;top:707px;width:1200px;height:570px;background:var(--light)}
.kicker{font-family:"Exo 2",sans-serif;font-size:21px;font-weight:400;color:var(--ink)}
.about-title{font-family:"Exo 2",sans-serif;font-size:40px;font-weight:700;color:#444}
.about-title span{color:var(--green)}
.body-text{font-size:15.5px;line-height:27.5px;color:#444}
.btn-outline{border:2px solid var(--green);color:var(--green);font-weight:700;font-size:17px}

/* what we do */
.what{position:absolute;left:0;top:1277px;width:1200px;height:514px}
.what-text{color:var(--white)}
.what-title{font-family:"Exo 2",sans-serif;font-size:36px;font-weight:700;line-height:1}
.what-title em{font-style:italic}
.what-para{font-size:13.5px;line-height:22.5px}

/* why */
.section-title{font-family:"Exo 2",sans-serif;font-weight:700;font-size:30px;letter-spacing:3px;color:var(--ink);text-align:center;width:1200px}
.section-title em{color:var(--green);font-style:italic;font-weight:800}
.feature{position:absolute;width:290px;text-align:center}
.feature-photo{width:250px;height:250px;border-radius:50%;margin:0 auto}
.feature h3{font-family:"Lato",sans-serif;font-weight:700;font-size:19px;color:var(--ink);margin-top:34px}
.feature p{font-size:14px;line-height:21px;color:var(--muted);margin-top:4px}

/* news */
.news{position:absolute;left:0;top:2349px;width:1200px;height:591px;background:var(--light)}
.news-card{position:absolute;top:119px;width:299px;height:369px;background:var(--white);box-shadow:0 2px 6px rgba(0,0,0,.08)}
.news-photo{height:175px}
.news-date{position:absolute;left:24px;top:193px;width:40px;height:46px;background:var(--green);color:var(--white);text-align:center;font-family:"Lato",sans-serif}
.news-date b{display:block;font-size:21px;line-height:24px;font-weight:700;margin-top:2px}
.news-date small{display:block;font-size:13px;line-height:15px}
.news-title{position:absolute;left:89px;top:194px;font-size:18px;line-height:24px;color:#666}
.news-body{position:absolute;left:25px;top:260px;width:260px;font-size:12.5px;line-height:18px;color:#666}
.news-more{position:absolute;left:25px;top:325px;font-size:12.5px;font-weight:900;color:var(--ink)}

/* cta */
.cta{position:absolute;left:0;top:2940px;width:1200px;height:387px;background:var(--slate)}
.cta-title{font-family:"Exo 2",sans-serif;font-size:27px;font-weight:700;letter-spacing:2px;line-height:37px;color:var(--white)}
.cta-text{font-size:17px;line-height:24px;color:var(--white)}

/* footer */
.site-footer{position:absolute;left:0;top:3327px;width:1200px;height:340px;background:var(--white)}
.foot-brand{position:absolute;left:136px;top:68px;width:170px;text-align:center}
.foot-brand .brand-dot{width:100px;height:100px;margin:0 auto 10px}
.foot-brand .brand-name{font-size:40px}
.foot-col{position:absolute;top:60px}
.foot-col h4{font-family:"Lato",sans-serif;font-size:15px;font-weight:700;color:var(--ink);margin-bottom:12px}
.foot-col li{list-style:none;font-size:13px;line-height:24.5px;color:#555}
.contact-item{display:flex;gap:10px;font-size:13px;line-height:15px;color:#444;margin-bottom:17px}
.contact-item svg{flex:none;margin-top:1px}
.social li{display:flex;align-items:center;gap:10px;line-height:31px;font-size:14px}
.social i{width:21px;height:21px;border-radius:50%;background:#1f8fd0;display:block}
.foot-rule{position:absolute;left:0;top:286px;width:1200px;height:1px;background:var(--rule)}
.copyright{position:absolute;top:300px;width:1200px;text-align:center;font-size:13px;color:#444}
</style>
</head>
<body>

<header class="site-header">
  <div class="brand" style="left:74px;top:12px">
    <div class="brand-dot"></div>
    <div class="brand-name">BRAVOLY</div>
  </div>
  <div class="nav-bar"></div>
  <nav class="main-nav">
    <a class="active" style="left:433px">ABOUT US</a>
    <a style="left:541px">SERVICES</a>
    <a style="left:646px">WHY US</a>
    <a style="left:739px">NEWS</a>
    <a style="left:816px">SUPPORT</a>
    <a style="left:918px">CONTACT US</a>
  </nav>
  <svg class="abs" style="left:1057px;top:35px" width="20" height="20" viewBox="0 0 20 20"><circle cx="8" cy="8" r="6" fill="none" stroke="#7dc03a" stroke-width="2"/><line x1="12.5" y1="12.5" x2="18" y2="18" stroke="#7dc03a" stroke-width="2.2" stroke-linecap="round"/></svg>
</header>

<section class="hero" role="img" aria-label="Photo of a scrapyard full of stacked wrecked cars and bumpers">
  <div class="hero-circle">
    <div class="hero-kicker">WELCOME TO</div>
    <div class="hero-title">BRAVOLY</div>
    <p class="hero-text">Nunc tempus felis vitae urna Vivamus porttitor neque at volutpat</p>
    <span class="btn btn-white hero-btn">Learn More</span>
  </div>
  <div class="slide-arrow" style="left:16px"><svg width="42" height="42" viewBox="0 0 42 42"><path d="M24 14l-7 7 7 7" fill="none" stroke="#333" stroke-width="2.5"/></svg></div>
  <div class="slide-arrow" style="left:1126px"><svg width="42" height="42" viewBox="0 0 42 42"><path d="M18 14l7 7-7 7" fill="none" stroke="#333" stroke-width="2.5"/></svg></div>
</section>

<section class="about">
  <svg class="abs" style="left:0;top:0" width="1200" height="570" viewBox="0 0 1200 570">
    <defs>
      <linearGradient id="aboutPhoto" x1="0" y1="0" x2="1" y2="1">
        <stop offset="0" stop-color="#8d959b"/><stop offset="1" stop-color="#5f676c"/>
      </linearGradient>
    </defs>
    <rect x="1146" y="0" width="54" height="570" fill="#e6e6e6"/>
    <path role="img" aria-label="Photo of a car scrapyard" d="M935 0H1200V520Q1200 528 1192 528H860Q845 528 835 516L680 340Q669 326 672 300L676 240Q678 222 690 208Z" fill="url(#aboutPhoto)"/>
    <circle cx="907" cy="289" r="180" fill="none" stroke="#fff" stroke-width="14"/>
  </svg>
  <div class="kicker abs" style="left:139px;top:107px">WHO WE ARE</div>
  <div class="about-title abs" style="left:136px;top:133px">ABOUT <span>BRAVOLY</span></div>
  <p class="body-text abs" style="left:138px;top:201px;width:480px">Nunc tempus felis vitae urna Vivamus porttitor neque at volutpat rutrum purus nisi eleifend libero a tempus libero lectus feugiat felis Morbi diam mauris viverra in gravida eu mattis in</p>
  <p class="body-text abs" style="left:138px;top:314px;width:480px">nonummy nibh ligula pulvinar metus eget consectetuer augue nisi quis lacus Ut ac mi quis lacus mollis aliquam Curabitu</p>
  <span class="btn btn-outline abs" style="left:138px;top:403px;width:208px;height:50px">LEARN MORE</span>
</section>

<section class="what">
  <svg class="abs" style="left:0;top:0" width="1200" height="514" viewBox="0 0 1200 514">
    <defs>
      <linearGradient id="whatPhoto" x1="0" y1="0" x2="0" y2="1">
        <stop offset="0" stop-color="#3f86c8"/><stop offset=".55" stop-color="#7fb0d8"/><stop offset="1" stop-color="#5a5560"/>
      </linearGradient>
    </defs>
    <rect width="1200" height="514" fill="#82c03e"/>
    <path d="M0 0H560Q690 250 540 514H0Z" fill="#fff"/>
    <path d="M0 0H548Q672 250 525 514H0Z" fill="#82c03e"/>
    <path role="img" aria-label="Photo of a crane grabber lifting a crushed car over a scrap pile" d="M0 0H540Q658 250 510 514H0Z" fill="url(#whatPhoto)"/>
  </svg>
  <div class="what-text abs" style="left:722px;top:104px;width:380px">
    <div class="kicker" style="color:#fff;font-size:23px">WHAT WE DO</div>
    <div class="what-title" style="margin-top:10px">AUTO <em>RECYCLING</em></div>
    <p class="what-para" style="margin-top:23px">Curabitur vel mi sit amet magna malesuada ultrices Ut nisi erat fermentum vel congue id euismod in elit</p>
    <p class="what-para" style="margin-top:23px">Fusce ultricies orci ac feugiat suscipit leo massa sodales velit et scelerisque quam Curabitur vel dolor ultrices ipsum dictum tristique Prae</p>
    <span class="btn btn-white" style="margin-top:24px;width:157px;height:41px;font-size:13px">Learn More</span>
  </div>
</section>

<section>
  <h2 class="section-title abs" style="left:0;top:1836px">WHY WE ARE</h2>
  <div class="feature" style="left:143px;top:1908px">
    <div class="feature-photo" role="img" aria-label="Photo of stacked alloy car wheels" style="background:radial-gradient(circle at 40% 60%,#c9ccd0,#6f7377)"></div>
    <h3>RECYCLING ANY CAR</h3>
    <p>Fusce ultricies orci ac feugiat suscipit leo massa sodales velit et scelerisque quam Curabitur vel dolor ult</p>
  </div>
  <div class="feature" style="left:466px;top:1908px">
    <div class="feature-photo" role="img" aria-label="Photo of a silver car with open trunk" style="background:radial-gradient(circle at 50% 55%,#b7bec6,#5b6670)"></div>
    <h3>PICK UP YOUR CAR</h3>
    <p>Fusce ultricies orci ac feugiat suscipit leo massa sodales velit et scelerisque quam Curabitur vel dolor ult</p>
  </div>
  <div class="feature" style="left:795px;top:1908px">
    <div class="feature-photo" role="img" aria-label="Photo of wrecked cars in an open scrapyard" style="background:linear-gradient(#dfe6ec 0%,#9aa4a2 40%,#4c5258 100%)"></div>
    <h3>ENVIORMENT FRIENDLY</h3>
    <p>Fusce ultricies orci ac feugiat suscipit leo massa sodales velit et scelerisque quam Curabitur vel dolor ult</p>
  </div>
</section>

<section class="news">
  <h2 class="section-title abs" style="left:0;top:49px">LATEST <em>NEWS</em></h2>
  <article class="news-card" style="left:118px">
    <div class="news-photo" role="img" aria-label="Photo of scrap cars on a tow truck" style="background:linear-gradient(#2f5d8c,#6a5a48)"></div>
    <div class="news-date"><b>20</b><small>JAN</small></div>
    <div class="news-title">Pellentesque faucibus<br>Ut accumsan ultric</div>
    <p class="news-body">Duis quam Nam eget lacus Aliquam erat volutpat Quisque dignissim congue leo Mauris vel lacus vitae felis vestibulum</p>
    <div class="news-more">READ MORE</div>
  </article>
  <article class="news-card" style="left:457px">
    <div class="news-photo" role="img" aria-label="Photo of a crushed scrap block on a loader" style="background:linear-gradient(135deg,#8a8f96,#c47a30 70%,#6b6f73)"></div>
    <div class="news-date"><b>10</b><small>JAN</small></div>
    <div class="news-title">Pellentesque faucibus<br>Ut accumsan ultric</div>
    <p class="news-body">Duis quam Nam eget lacus Aliquam erat volutpat Quisque dignissim congue leo Mauris vel lacus vitae felis vestibulum</p>
    <div class="news-more">READ MORE</div>
  </article>
  <article class="news-card" style="left:796px">
    <div class="news-photo" role="img" aria-label="Photo of colourful cars stacked on racks" style="background:linear-gradient(#9aa0a8,#b8344a 55%,#3f8a6c)"></div>
    <div class="news-date"><b>02</b><small>JAN</small></div>
    <div class="news-title">Pellentesque faucibus<br>Ut accumsan ultric</div>
    <p class="news-body">Duis quam Nam eget lacus Aliquam erat volutpat Quisque dignissim congue leo Mauris vel lacus vitae felis vestibulum</p>
    <div class="news-more">READ MORE</div>
  </article>
</section>

<section class="cta">
  <svg class="abs" style="left:0;top:0" width="1200" height="387" viewBox="0 0 1200 387">
    <defs>
      <linearGradient id="ctaPhoto" x1="0" y1="0" x2="0" y2="1">
        <stop offset="0" stop-color="#4c8ed0"/><stop offset=".4" stop-color="#9cbcd8"/><stop offset="1" stop-color="#55585c"/>
      </linearGradient>
    </defs>
    <path d="M340 0Q470 190 365 387H0V0Z" fill="#fff"/>
    <path d="M335 0Q462 190 358 387H0V0Z" fill="#7dc03a"/>
    <path role="img" aria-label="Photo of rows of wrecked cars in a scrapyard" d="M320 0Q440 190 340 387H0V0Z" fill="url(#ctaPhoto)"/>
  </svg>
  <h2 class="cta-title abs" style="left:490px;top:90px;width:640px">CURABITUR VEL MI SIT AMET MAGNA MALESUADA ULTRICES</h2>
  <p class="cta-text abs" style="left:490px;top:179px;width:620px">Curabitur vel mi sit amet magna malesuada ultrices Ut nisi erat fermentum vel congue id euismod in elit Fusce ultricies orci ac feugiat</p>
  <span class="btn btn-white abs" style="left:488px;top:250px;width:177px;height:46px;font-size:14px">Contact Us</span>
</section>

<footer class="site-footer">
  <div class="foot-brand">
    <div class="brand-dot"></div>
    <div class="brand-name">BRAVOLY</div>
  </div>
  <div class="foot-col" style="left:373px">
    <h4>CONTACT US</h4>
    <div class="contact-item"><svg width="14" height="16" viewBox="0 0 14 16"><path d="M7 15s5-5 5-9A5 5 0 0 0 2 6c0 4 5 9 5 9z" fill="none" stroke="#333" stroke-width="1.4"/><circle cx="7" cy="6" r="1.8" fill="#333"/></svg><span>48 Ferrow Lane #12<br>Dalton 55810</span></div>
    <div class="contact-item"><svg width="14" height="14" viewBox="0 0 14 14"><path d="M3 1l2 3-1.5 1.5a8 8 0 0 0 5 5L10 9l3 2-1.5 2.5C6 13 1 8 .8 2.5z" fill="none" stroke="#333" stroke-width="1.3"/></svg><span>555.014.7720</span></div>
    <div class="contact-item"><svg width="15" height="12" viewBox="0 0 15 12"><rect x="1" y="1" width="13" height="10" fill="none" stroke="#333" stroke-width="1.3"/><path d="M1 1l6.5 5.5L14 1" fill="none" stroke="#333" stroke-width="1.3"/></svg><span>hello@bravoly.com</span></div>
  </div>
  <div class="foot-col" style="left:620px">
    <h4>COMPANY</h4>
    <ul><li>Home</li><li>About us</li><li>Services</li><li>Why Us</li><li>Contact</li></ul>
  </div>
  <div class="foot-col" style="left:780px">
    <h4>RESOURCES</h4>
    <ul><li>Support</li><li>News</li><li>Term of Use</li><li>Privacy Policy</li></ul>
  </div>
  <div class="foot-col" style="left:954px">
    <h4>GET IN TOUCH</h4>
    <ul class="social">
      <li><i></i>Chirply</li>
      <li><i style="background:#3b5a98"></i>Facespace</li>
      <li><i style="background:#1674b3"></i>Linkedly</li>
      <li><i style="background:#3d5a80"></i>Snapgram</li>
    </ul>
  </div>
  <div class="foot-rule"></div>
  <div class="copyright">Copyright © 2020 All right reserved</div>
</footer>

</body>
</html>
```